Evaporative Air Conditioning Summer Service

Would like to design a flyer to send out in an email to existing clients to promote a Pre-summer service for Evaporative Air Conditioners
Cost will be $110.00 inc gst
Tasks included in service are
- Inspection and clean of pads
- Inspection and check float valve, water pump, fan, motor, bearings, drain
- Clean basin
- Supply of bacterial tablet
- Inspect overall condition of unit
- Any repairs if required will be quoted
Please see files attached of a previous very basic flyer I have used for installation and replacement unit costs. This has current contact information
Have also uploaded company logo for use.
Thanks
Plumbing

```html
<!DOCTYPE html>
<html lang="en">
<head>
<meta charset="utf-8">
<title>Evaporative Air Conditioning Summer Service – Summit Gas &amp; Plumbing</title>
<link href="https://fonts.googleapis.com/css2?family=Jura:wght@500;600;700&family=Montserrat:wght@800&display=swap" rel="stylesheet">
<style>
  :root {
    --navy: #1a1d8f;
    --navy-deep: #14127a;
    --navy-light: #2a2ea3;
    --brand-blue: #2f86dc;
    --orange: #f7a21b;
    --red: #b8262a;
    --paper: #f1f1f1;
    --ink: #111111;
    --worker-tone: #3b6fc4;
    --woman-tone: #f2b04a;
    --bubble: #d9d6ec;
    --stripe: #f4d21c;
  }
  * { margin: 0; padding: 0; box-sizing: border-box; }
  html, body { width: 848px; height: 1200px; overflow: hidden; background: #ffffff; }
  .flyer {
    position: relative; width: 848px; height: 1200px; overflow: hidden;
    background: var(--paper);
    font-family: "Jura", sans-serif;
  }
  .header {
    position: absolute; left: 0; top: 0; width: 848px; height: 150px;
    background: linear-gradient(160deg, var(--navy-deep) 0%, var(--navy-deep) 55%, var(--navy-light) 55.2%, var(--navy-light) 100%);
  }
  .brand {
    position: absolute; display: flex; align-items: center; gap: 14px;
    font-family: "Montserrat", sans-serif; font-weight: 800; color: var(--brand-blue);
    text-transform: uppercase;
  }
  .brand-mark { border-radius: 50%; background: var(--orange); flex: none; }
  .brand-name { line-height: 0.95; }
  .brand--header { left: 125px; top: 26px; font-size: 50px; }
  .brand--header .brand-mark { width: 52px; height: 52px; }
  .brand--footer { left: 560px; top: 1124px; font-size: 22px; gap: 8px; }
  .brand--footer .brand-mark { width: 26px; height: 26px; }

  .art { position: absolute; }
  .art--worker { left: 58px; top: 182px; width: 236px; height: 290px;
    background: linear-gradient(180deg, #cfe0f7 0%, var(--worker-tone) 60%, #a9b5d8 100%); border-radius: 10px; }
  .art--woman { left: 712px; top: 517px; width: 90px; height: 264px;
    background: linear-gradient(180deg, #8a4a3a 0%, var(--woman-tone) 30%, #4a3f5c 70%, #c7c3dd 100%); border-radius: 40px 40px 12px 12px; }

  .headline {
    position: absolute; left: 316px; width: 480px; top: 210px;
    text-align: center; color: var(--red); font-weight: 600; font-size: 25px; line-height: 40px;
    letter-spacing: 1px; text-transform: uppercase; white-space: nowrap;
  }
  .pitch {
    position: absolute; left: 340px; width: 452px; top: 296px;
    text-align: center; color: var(--navy); font-weight: 600; font-size: 19px; line-height: 34px;
    letter-spacing: 2px; text-transform: uppercase; list-style: none; white-space: nowrap;
  }
  .pitch .pitch-dark { color: var(--ink); }

  .price-badge {
    position: absolute; left: 65px; top: 491px; width: 205px; height: 103px;
    background: linear-gradient(155deg, var(--navy-deep) 0%, var(--navy-deep) 40%, var(--navy-light) 40.3%);
    border-radius: 52px 52px 0 52px; color: #fff; text-align: center;
  }
  .price-label { font-size: 26px; font-weight: 600; letter-spacing: 2px; margin-top: 14px; line-height: 30px; }
  .price-row { font-size: 30px; font-weight: 600; line-height: 42px; }
  .price-old { color: var(--orange); text-decoration: line-through; }
  .price-sep { margin: 0 12px; opacity: .8; }

  .bubble {
    position: absolute; left: 578px; top: 557px; width: 124px; height: 66px;
    background: var(--bubble); border-radius: 34px; color: var(--red);
    font-size: 16px; font-weight: 600; text-align: center; line-height: 20px; padding-top: 13px; letter-spacing: 1px;
  }
  .bubble::after {
    content: ""; position: absolute; right: -14px; top: 26px;
    border-left: 18px solid var(--bubble); border-top: 8px solid transparent; border-bottom: 8px solid transparent;
  }

  .offer {
    position: absolute; left: 59px; top: 676px; color: var(--red);
    font-size: 25px; font-weight: 600; letter-spacing: 1px; white-space: nowrap;
  }
  .services { position: absolute; left: 114px; top: 747px; width: 600px; list-style: none; }
  .services li {
    position: relative; padding-left: 80px; color: var(--red); white-space: nowrap;
    font-size: 20px; font-weight: 600; line-height: 37.6px; letter-spacing: 1.4px;
  }
  .services svg { position: absolute; left: 0; top: 7px; width: 32px; height: 24px; }

  .footer {
    position: absolute; left: 0; top: 1045px; width: 848px; height: 155px;
    background: linear-gradient(172deg, var(--navy-light) 0%, var(--navy-light) 30%, var(--navy-deep) 30.3%);
    border-bottom: 4px solid var(--stripe); color: #fff;
  }
  .footer-title { position: absolute; left: 0; width: 848px; top: 10px; text-align: center; font-size: 22px; font-weight: 600; letter-spacing: 3px; text-transform: uppercase; }
  .contact { position: absolute; left: 44px; display: flex; align-items: center; gap: 22px; font-size: 17px; font-weight: 600; letter-spacing: 1.2px; }
  .contact svg { width: 34px; height: 34px; flex: none; }
  .contact--phone { top: 56px; }
  .contact--email { top: 112px; }
  .abn { position: absolute; left: 610px; top: 47px; font-size: 18px; font-weight: 600; letter-spacing: 1.5px; }
</style>
</head>
<body>
<main class="flyer">
  <header class="header">
    <div class="brand brand--header">
      <span class="brand-mark"></span>
      <span class="brand-name">Summit Gas<br>&amp; Plumbing</span>
    </div>
  </header>

  <div class="art art--worker" role="img" aria-label="Illustration of a technician in blue overalls servicing a wall-mounted air conditioner with a toolbox beside him"></div>

  <h1 class="headline">Evaporative Air Conditioning<br>Summer Service</h1>
  <ul class="pitch">
    <li>Book our</li>
    <li class="pitch-dark">Pre-summer service package</li>
    <li>at discounted price</li>
    <li>and enjoy</li>
    <li>the all new fresh air.</li>
  </ul>

  <div class="price-badge">
    <p class="price-label">cost</p>
    <p class="price-row"><span class="price-old">$150</span><span class="price-sep">|</span><span>$110</span></p>
  </div>

  <div class="bubble">What do<br>you offer?</div>
  <div class="art art--woman" role="img" aria-label="Illustration of a thoughtful woman in a yellow top wondering what the service includes"></div>

  <h2 class="offer">We will provide all these services in just $110</h2>
  <ul class="services">
    <li><svg viewBox="0 0 32 24"><rect x="10" y="2" width="20" height="18" rx="4" fill="#f7a21b"/><path d="M2 14 L8 21 L24 3" fill="none" stroke="#111" stroke-width="2.5"/></svg>Inspection and clean of pads</li>
    <li><svg viewBox="0 0 32 24"><rect x="10" y="2" width="20" height="18" rx="4" fill="#f7a21b"/><path d="M2 14 L8 21 L24 3" fill="none" stroke="#111" stroke-width="2.5"/></svg>Inspection and check float valve, water pump,<br>fan, motor, bearings, drain</li>
    <li><svg viewBox="0 0 32 24"><rect x="10" y="2" width="20" height="18" rx="4" fill="#f7a21b"/><path d="M2 14 L8 21 L24 3" fill="none" stroke="#111" stroke-width="2.5"/></svg>Clean basin</li>
    <li><svg viewBox="0 0 32 24"><rect x="10" y="2" width="20" height="18" rx="4" fill="#f7a21b"/><path d="M2 14 L8 21 L24 3" fill="none" stroke="#111" stroke-width="2.5"/></svg>Supply of bacterial tablet</li>
    <li><svg viewBox="0 0 32 24"><rect x="10" y="2" width="20" height="18" rx="4" fill="#f7a21b"/><path d="M2 14 L8 21 L24 3" fill="none" stroke="#111" stroke-width="2.5"/></svg>Inspect overall condition of unit</li>
    <li><svg viewBox="0 0 32 24"><rect x="10" y="2" width="20" height="18" rx="4" fill="#f7a21b"/><path d="M2 14 L8 21 L24 3" fill="none" stroke="#111" stroke-width="2.5"/></svg>Any repairs if required will be quoted</li>
  </ul>

  <footer class="footer">
    <p class="footer-title">- : Contact Info : -</p>
    <p class="contact contact--phone">
      <svg viewBox="0 0 24 24"><path fill="#fff" d="M6.6 10.8a15.1 15.1 0 0 0 6.6 6.6l2.2-2.2c.3-.3.7-.4 1-.2 1.1.4 2.3.6 3.6.6.6 0 1 .4 1 1V20c0 .6-.4 1-1 1A17 17 0 0 1 3 4c0-.6.4-1 1-1h3.5c.6 0 1 .4 1 1 0 1.3.2 2.5.6 3.6.1.3 0 .7-.2 1z"/></svg>
      0400 123 456
    </p>
    <p class="contact contact--email">
      <svg viewBox="0 0 24 24"><rect x="2" y="5" width="20" height="14" rx="1.5" fill="#fff"/><path d="M2.5 6 L12 13 L21.5 6" fill="none" stroke="#14127a" stroke-width="1.8"/></svg>
      office@summitgasplumbing.example
    </p>
    <p class="abn">ABN - 11 222 333 444</p>
  </footer>
  <div class="brand brand--footer">
    <span class="brand-mark"></span>
    <span class="brand-name">Summit Gas<br>&amp; Plumbing</span>
  </div>
</main>
</body>
</html>
```